Teaching Tool Design

This is a teaching evaluating tool so that teachers can assess how well they are teaching.
Please use the Explicit Instruction Classroom Observation Matrix as the text for the project.
Design a clean, visually aligned version of the Explicit Instruction Observation Matrix that reflects Tallowood’s instructional model and KIVU’s framework https://www.plovanetworks.example/sites/default/files/2022-08/doc-rubric-a2.pdf
Use a professional layout with clear column divisions, alternating row shading, and space for observer notes and teacher reflection.
Copy Tallowood's style theme https://tallowoodhs.example.edu/
Also please see the attached to make a similar style.

```html
<!DOCTYPE html>
<html lang="en">
<head>
<meta charset="utf-8">
<title>Explicit Instruction Observation Matrix – Tallowood</title>
<link href="https://fonts.googleapis.com/css2?family=Roboto+Condensed:wght@300;400;700&display=swap" rel="stylesheet">
<style>
  :root{
    --navy:#26358f;
    --yellow-light:#f3ee86;
    --yellow-dark:#c8b84a;
    --yellow-text:#f2e45a;
    --cell-top:#eceef2;
    --cell-bottom:#dcdfe5;
    --cell-text:#555a63;
    --page:#ffffff;
    --backdrop:#eceef1;
    --panel-grey:#e6e8ec;
  }
  *{box-sizing:border-box;margin:0;padding:0}
  html,body{width:854px;height:1200px;overflow:hidden}
  body{background:var(--backdrop);font-family:"Roboto Condensed","Arial Narrow",sans-serif;position:relative}

  .sheet{
    position:absolute;left:16px;top:310px;
    width:1305px;height:922px;
    background:var(--page);
    transform:scale(0.6306);transform-origin:0 0;
    box-shadow:0 6px 24px rgba(0,0,0,.18);
  }

  .matrix{
    position:absolute;left:20px;top:20px;width:1265px;
    display:grid;
    grid-template-columns:102px repeat(11,minmax(0,1fr));
    grid-template-rows:repeat(5,120px) 75px 76px;
    gap:4px;
  }

  .row-label{
    background:var(--navy);border-radius:7px 0 0 7px;
    color:#fff;font-weight:700;font-size:19px;
    display:flex;align-items:center;padding-left:12px;
  }
  .quality-label{grid-column:1;grid-row:1/6;align-items:flex-end;padding-bottom:16px;border-radius:7px 7px 0 7px;position:relative}
  .quality-label span{line-height:1.1}
  .quality-label svg{position:absolute;left:70px;bottom:16px}

  .criterion{
    background:linear-gradient(180deg,var(--cell-top),var(--cell-bottom));
    border-radius:6px;
    color:var(--cell-text);font-weight:300;font-size:10.8px;line-height:1.18;
    padding:9px 5px 4px 6px;
    overflow-wrap:break-word;
  }
  .criterion.tight{font-size:10px;line-height:1.15}

  .indicator{
    border-radius:6px;font-size:11px;line-height:1.18;font-weight:400;
    padding:9px 7px;
  }
  .indicator.gold{background:linear-gradient(100deg,var(--yellow-light),var(--yellow-dark));color:var(--navy)}
  .indicator.blue{background:var(--navy);color:var(--yellow-text)}

  .capability{
    border-radius:6px;display:flex;align-items:center;gap:16px;padding-left:6px;
    font-size:13px;line-height:1.25;font-weight:400;
  }
  .capability .num{
    width:38px;height:28px;border-radius:3px;display:flex;align-items:center;justify-content:center;
    font-weight:700;font-size:15px;color:#fff;flex:none;
  }
  .capability.gold{background:linear-gradient(100deg,var(--yellow-light),var(--yellow-dark));color:var(--navy)}
  .capability.gold .num{background:var(--navy)}
  .capability.blue{background:var(--navy);color:var(--yellow-text)}
  .capability.blue .num{background:linear-gradient(100deg,var(--yellow-light),var(--yellow-dark))}
  .capability .strong{font-weight:700}
  .cap-1{grid-column:2/5}.cap-2{grid-column:5/8}.cap-3{grid-column:8/11}.cap-4{grid-column:11/13}

  .footer-note{
    position:absolute;top:834px;height:52px;background:var(--panel-grey);border-radius:6px;
    display:flex;align-items:center;color:#3d424b;
  }
  .model-note{left:20px;width:330px;padding-left:14px;font-size:13.5px}
  .reading-note{left:950px;width:335px;padding-left:24px;font-size:11px;line-height:1.2;font-weight:300}

  .school-name{
    position:absolute;left:358px;top:840px;width:82px;height:40px;
    display:flex;align-items:center;gap:5px;
    font-weight:700;font-size:13px;color:var(--navy);
  }
  .school-name .mark{width:10px;height:10px;background:var(--navy);flex:none}
  .motto{
    position:absolute;left:440px;top:834px;width:500px;height:52px;
    background:var(--navy);border-radius:0 6px 6px 0;
    display:flex;align-items:center;padding-left:20px;
    color:var(--yellow-text);font-weight:700;font-size:27px;white-space:nowrap;
  }
</style>
</head>
<body>
<div class="sheet">
  <div class="matrix">
    <div class="row-label quality-label"><span>Quality<br>criteria</span>
      <svg width="14" height="60" viewBox="0 0 14 60" aria-hidden="true"><path d="M7 2v56H0M2 8l5-6 5 6" fill="none" stroke="#f2e45a" stroke-width="1.8"/></svg>
    </div>

    <div class="criterion">Anticipates critical points within the learning progression when formatively assessing student learning is most important</div>
    <div class="criterion"></div><div class="criterion"></div><div class="criterion"></div><div class="criterion"></div><div class="criterion"></div><div class="criterion"></div>
    <div class="criterion">Provides additional support that ensures students are optimally challenged in their learning</div>
    <div class="criterion"></div><div class="criterion"></div>
    <div class="criterion">Provides immediate feedback that does not reduce cognitive demand</div>

    <div class="criterion"></div>
    <div class="criterion">Identifies likely challenges and common misconceptions</div>
    <div class="criterion">Sequences chunked tasks based on the learning progression and evidence of what students already know and are able to do</div>
    <div class="criterion"></div><div class="criterion"></div>
    <div class="criterion">Refers to learning objectives and success criteria throughout the lesson, particularly when achieved</div>
    <div class="criterion">Sequences multiple worked examples to gradually introduce different elements of the task or alternative ways of completing it</div>
    <div class="criterion"></div>
    <div class="criterion">Gradually removes scaffolding based on evidence of student learning</div>
    <div class="criterion tight">Sequences opportunities for independent practice to gradually deepen students’ understanding of what they have learned</div>
    <div class="criterion"></div>

    <div class="criterion">Plans unit based on learning progression</div>
    <div class="criterion"></div>
    <div class="criterion">Sequences chunked tasks based on the learning progression</div>
    <div class="criterion">Tailors learning objectives from the curriculum for the whole class based on what students already know and are able to do</div>
    <div class="criterion">Sets clear success criteria and stretch goals for the whole class</div>
    <div class="criterion">Develops student understanding of learning objectives and success criteria</div>
    <div class="criterion"></div>
    <div class="criterion">Provides additional support based on evidence of what students already know and are able to do</div>
    <div class="criterion"></div><div class="criterion"></div><div class="criterion"></div>

    <div class="criterion">Consults the curriculum to identify the common learning progression for the target knowledge and skills</div>
    <div class="criterion">Identifies prerequisite knowledge and skills from the curriculum</div>
    <div class="criterion">Chunks learning into small, manageable tasks</div>
    <div class="criterion">Sets learning objectives from the curriculum for the whole class</div>
    <div class="criterion">Sets clear success criteria for the whole class</div>
    <div class="criterion">Shares learning objectives and success criteria for students</div>
    <div class="criterion">Walks students through all required steps for completing the task using worked examples</div>
    <div class="criterion">Explains knowledge and skills needed to complete the task</div>
    <div class="criterion">Presents some worked examples with removed steps</div>
    <div class="criterion">Provides opportunities for independent practice</div>
    <div class="criterion">Provides immediate feedback to students as they practise</div>

    <div class="criterion">I am yet to include any of these behaviours in my explicit instruction practice</div>
    <div class="criterion">I am yet to include any of these behaviours in my explicit instruction practice</div>
    <div class="criterion">I am yet to include any of these behaviours in my explicit instruction practice</div>
    <div class="criterion">I am yet to include any of these behaviours in my explicit instruction practice</div>
    <div class="criterion">I am yet to include any of these behaviours in my explicit instruction practice</div>
    <div class="criterion">I am yet to include any of these behaviours in my explicit instruction practice</div>
    <div class="criterion">I am yet to include any of these behaviours in my explicit instruction practice</div>
    <div class="criterion">I am yet to include any of these behaviours in my explicit instruction practice</div>
    <div class="criterion">I am yet to include any of these behaviours in my explicit instruction practice</div>
    <div class="criterion">I am yet to include any of these behaviours in my explicit instruction practice</div>
    <div class="criterion">I am yet to include any of these behaviours in my explicit instruction practice</div>

    <div class="row-label">Indicator</div>
    <div class="indicator gold">Identifies learning progressions from the curriculum</div>
    <div class="indicator gold">Identifies how knowledge and skills build</div>
    <div class="indicator gold">Chunks learning</div>
    <div class="indicator blue">Sets learning objectives</div>
    <div class="indicator blue">Sets success criteria</div>
    <div class="indicator blue">Communicates learning objectives and success criteria</div>
    <div class="indicator gold">Uses worked examples</div>
    <div class="indicator gold">Provides scaffolding when needed</div>
    <div class="indicator gold">Removes scaffolding as needed</div>
    <div class="indicator blue">Provides opportunities for independent practice</div>
    <div class="indicator blue">Interacts with students during practice</div>

    <div class="row-label">Capability</div>
    <div class="capability gold cap-1"><span class="num">1</span><span>Breaks down complex skills and knowledge<br>into smaller instructional tasks</span></div>
    <div class="capability blue cap-2"><span class="num">2</span><span>Sets clear and measurable learning<br>objectives and success criteria</span></div>
    <div class="capability gold cap-3"><span class="num">3</span><span>Uses worked examples to demonstrate<br>what students need to learn</span></div>
    <div class="capability blue cap-4"><span class="num">4</span><span class="strong">Provides opportunities for<br>students to practise what<br>they have learned</span></div>
  </div>

  <div class="footer-note model-note">Tallowood’s Instructional Model and KIVU’s Framework</div>
  <div class="school-name"><span class="mark"></span>Tallowood</div>
  <div class="motto">We Believe. We Strive. We Achieve.</div>
  <div class="footer-note reading-note">Read the capability and the related criteria. For each capability,<br>identify which criterion best describes your current practice.</div>
</div>
</body>
</html>
```